business card

Business card for new business.
Red and black corporate colors.
Card can have an Indsutrial feel to it. Feel free to add Rust, Bolted steel, or graphics as you see fit. We provide highly specialized services to the below mentioned industries.
Keep information out of corners so that if I want I can choose rounded corners.
Information
- front. name - title - phone - email
- Rear
Forging - Port - Fabrication - Quarry - Power
Ridgeford - Marrow Bay - Port Ellsworth - Stonebridge - Westhollow

```html
<!DOCTYPE html>
<html lang="en">
<head>
<meta charset="UTF-8">
<title>Girderline Business Card</title>
<link rel="stylesheet" href="https://fonts.googleapis.com/css2?family=Open+Sans:wght@400;600&family=Roboto+Condensed:wght@400;700&display=swap">
<style>
  :root {
    --backdrop: #2b2b2c;
    --card-dark: #1f2326;
    --card-dark-edge: #2a2f33;
    --card-light: #f6f6f6;
    --brand-red: #e01b22;
    --logo-grey: #b9b9b9;
    --text-light: #ffffff;
    --text-grey: #6d6d6d;
    --text-dark: #3b3b3b;
    --divider: #cfcfcf;
  }
  * { box-sizing: border-box; margin: 0; padding: 0; }
  html, body { width: 1200px; height: 900px; overflow: hidden; }
  body {
    background: var(--backdrop);
    display: flex;
    flex-direction: column;
    align-items: center;
    justify-content: center;
    gap: 40px;
    font-family: "Open Sans", sans-serif;
  }
  .card {
    width: 640px;
    height: 366px;
    position: relative;
    box-shadow: 0 10px 30px rgba(0,0,0,0.45);
  }
  .card-back {
    background: linear-gradient(160deg, var(--card-dark-edge), var(--card-dark));
    display: flex;
    flex-direction: column;
    align-items: center;
    justify-content: center;
    gap: 28px;
  }
  .brand {
    display: flex;
    align-items: center;
    gap: 14px;
  }
  .brand-mark {
    width: 22px;
    height: 22px;
    background: var(--brand-red);
  }
  .brand-name {
    font-family: "Roboto Condensed", sans-serif;
    font-weight: 700;
    font-size: 64px;
    letter-spacing: 1px;
    color: var(--logo-grey);
    line-height: 1;
  }
  .services {
    text-align: center;
    color: var(--text-light);
    font-size: 16px;
    line-height: 1.45;
  }
  .services .dot {
    color: var(--brand-red);
    margin: 0 4px;
  }
  .card-front {
    background: var(--card-light);
    display: flex;
    align-items: center;
    justify-content: center;
    gap: 30px;
  }
  .person { text-align: right; }
  .person-name {
    font-family: "Roboto Condensed", sans-serif;
    font-weight: 700;
    font-size: 34px;
    color: var(--brand-red);
    line-height: 1.05;
  }
  .person-title {
    font-size: 15px;
    color: var(--text-grey);
    letter-spacing: 0.5px;
  }
  .divider {
    width: 1px;
    height: 82px;
    background: var(--divider);
  }
  .contact { list-style: none; }
  .contact li {
    display: flex;
    align-items: center;
    gap: 10px;
    font-size: 16px;
    color: var(--text-dark);
    line-height: 1.6;
  }
  .contact svg { width: 14px; height: 14px; fill: var(--brand-red); flex: none; }
</style>
</head>
<body>
  <section class="card card-back">
    <div class="brand">
      <span class="brand-mark"></span>
      <span class="brand-name">GIRDERLINE</span>
    </div>
    <p class="services">
      Forging<span class="dot">•</span>Port<span class="dot">•</span>Fabrication<span class="dot">•</span>Quarry<br>
      Power<span class="dot">•</span>Ridgeford<span class="dot">•</span>Marrow Bay<span class="dot">•</span>Port Ellsworth<br>
      Stonebridge<span class="dot">•</span>Westhollow
    </p>
  </section>

  <section class="card card-front">
    <div class="person">
      <h1 class="person-name">MARK HALDEN</h1>
      <p class="person-title">PRESIDENT</p>
    </div>
    <div class="divider"></div>
    <ul class="contact">
      <li>
        <svg viewBox="0 0 16 16" aria-hidden="true"><path d="M1 5c0-2 3-3 7-3s7 1 7 3v1h-4V5H5v1H1z M3 8h10l1 6H2z"/><circle cx="8" cy="11" r="1.6" fill="#f6f6f6"/></svg>
        555 0142 7788
      </li>
      <li>
        <svg viewBox="0 0 16 16" aria-hidden="true"><path d="M1 3h14v1L8 9 1 4z M1 6l7 5 7-5v7H1z"/></svg>
        mark@girderline.com
      </li>
      <li>
        <svg viewBox="0 0 16 16" aria-hidden="true"><circle cx="8" cy="8" r="7"/><path d="M1 8h14M8 1c-3 3-3 11 0 14M8 1c3 3 3 11 0 14" stroke="#f6f6f6" stroke-width="1" fill="none"/></svg>
        www.girderline.com
      </li>
    </ul>
  </section>
</body>
</html>
```